I created a company name KORLUNE and I sell cell phone cases. I'm interesting for a great package and

I need a packaging design for a new company based in Quebec City called KORLUNE. I have a supplier in China and I need a good design for my cell phones cases product. I want a black design with a red. The final design should tell the customer I WANT TO BUY THAT CASE.

Target Market(s)

Everyone who has a cell phone

Industry/Entity Type

Cell Phone

Font styles to use
Sans Serif
Other font styles liked:
• I want script original to stand out from the competition

Colors

Designer to choose colors to be used in the design.

Requirements
Must have
• Black and red. I want have look like the photo I just send. I want it with red. Just look at the photo and try to design similar like this, but not the same.
Nice to have
• My company name in the middle. I want it in white. Design me a packaging cases I feel like I want to buy it.

```html
<!DOCTYPE html>
<html lang="en">
<head>
<meta charset="utf-8">
<title>KORLUNE Phone Cover Packaging</title>
<link rel="stylesheet" href="https://fonts.googleapis.com/css2?family=Archivo+Black&family=Archivo:wght@700&display=swap">
<style>
  :root {
    --paper: #ffffff;
    --card-red: #ec1c24;
    --ink: #0d0d0d;
    --case-navy: #3d4863;
    --case-navy-deep: #2c3449;
    --icon-amber: #f7941d;
  }
  html, body {
    margin: 0;
    padding: 0;
    width: 999px;
    height: 1200px;
    overflow: hidden;
    background: var(--paper);
  }
  .package {
    position: relative;
    width: 999px;
    height: 1200px;
  }
  .package-art {
    position: absolute;
    inset: 0;
    display: block;
  }
  .brand-name {
    font-family: "Archivo Black", "Arial Black", sans-serif;
    fill: var(--ink);
  }
  .product-label {
    font-family: "Archivo", Arial, sans-serif;
    font-weight: 700;
    fill: var(--ink);
  }
</style>
</head>
<body>
<main class="package">
  <svg class="package-art" viewBox="0 0 999 1200" width="999" height="1200" xmlns="http://www.w3.org/2000/svg">
    <defs>
      <linearGradient id="caseTone" x1="0" y1="0" x2="1" y2="1">
        <stop offset="0" stop-color="var(--case-navy)"/>
        <stop offset="1" stop-color="var(--case-navy-deep)"/>
      </linearGradient>
    </defs>

    <!-- hanger tab -->
    <rect class="hanger-tab" x="215" y="30" width="570" height="110" fill="var(--card-red)"/>
    <rect class="hanger-slot" x="390" y="75" width="203" height="31" rx="15.5" fill="var(--paper)"/>

    <!-- card body -->
    <rect class="card-body" x="205" y="135" width="590" height="1035" fill="var(--card-red)"/>

    <!-- display window -->
    <rect class="display-window" x="275" y="300" width="447" height="760" fill="var(--paper)"/>

    <!-- product shown through window -->
    <rect class="product-case" role="img" aria-label="Navy blue rugged phone case with black bumpers seen through the window"
          x="292" y="380" width="415" height="680" rx="34" fill="url(#caseTone)"/>

    <!-- header: black crescent beneath red panel -->
    <path class="header-crescent" d="M205,135 H795 V268 Q500,548 205,282 Z" fill="var(--ink)"/>
    <path class="header-panel" d="M205,135 H795 V262 Q500,478 205,262 Z" fill="var(--card-red)"/>
    <text class="brand-name" x="500" y="292" text-anchor="middle" font-size="90" textLength="335" lengthAdjust="spacingAndGlyphs">KORLUNE</text>

    <!-- bottom dome -->
    <path class="footer-dome" d="M275,1048 Q500,935 722,1048 L722,1060 L275,1060 Z" fill="var(--card-red)"/>
    <rect class="footer-panel" x="205" y="1055" width="590" height="115" fill="var(--card-red)"/>

    <!-- cover icon -->
    <g class="cover-icon">
      <rect x="466" y="991" width="68" height="92" rx="4" fill="var(--ink)" stroke="var(--icon-amber)" stroke-width="2"/>
      <rect x="472" y="1000" width="56" height="68" fill="var(--card-red)"/>
      <circle cx="500" cy="1075" r="4" fill="var(--card-red)"/>
    </g>
    <text class="product-label" x="500" y="1128" text-anchor="middle" font-size="18">COVER</text>
  </svg>
</main>
</body>
</html>
```